Business Card Design Project

This is the first time we use our new logo. We need a business card that we can use both on our institutional corporate relationships and also that works for our staff that deals with consumers directly.

VELUNDA is a new company dedicated to empower consumers and to provide them with the best choices for specialized health care using the latest telemedicine technology (medicine at a distance via videoconference).

We want to print this cards in high quality materials and process. We will like designs that allow us to use UV spot varnish and other techniques that will differentiate us.

We are including Two different versions of Color logos. In addition we are including white over black background logos. Those can be used replacing the black for a color.

Please note this is the first time we will be creating any corporate materials with our new logo and colors.

Target Market(s)

34+ consumers of medium high and high socioeconomic levels.

Industry/Entity Type

Health

Requirements
Must have
• Our logo on its original colors
Should not have
• Any other graphical element or design that is not our logo

```html
<!DOCTYPE html>
<html lang="en">
<head>
<meta charset="utf-8">
<title>Velunda Business Card</title>
<link href="https://fonts.googleapis.com/css2?family=Montserrat:wght@400;700&family=Arimo:wght@400;700&display=swap" rel="stylesheet">
<style>
  :root {
    --backdrop: #e9e6e1;
    --card-white: #ffffff;
    --brand-navy: #1d5580;
    --brand-sky: #5ab4dc;
    --brand-blue: #2f6fb4;
    --ink: #333333;
    --divider: #c9c9c9;
    --back-blue: #1b5680;
  }
  * { margin: 0; padding: 0; box-sizing: border-box; }
  html, body { width: 1200px; height: 1057px; overflow: hidden; background: var(--backdrop); }
  .stage { position: relative; width: 1200px; height: 1057px; }
  .card {
    position: absolute; left: 190px; width: 820px; height: 469px;
    box-shadow: 0 6px 18px rgba(0,0,0,0.18);
    overflow: hidden;
  }
  .card--front { top: 44px; background: var(--card-white); }
  .card--back { top: 544px; background: var(--back-blue); }

  .brand { position: absolute; left: 70px; top: 150px; display: flex; align-items: center; gap: 22px; }
  .brand__dot { width: 60px; height: 60px; border-radius: 50%; background: var(--brand-blue); }
  .brand__name {
    font-family: "Montserrat", sans-serif; font-weight: 700; font-size: 66px;
    letter-spacing: 5px; color: var(--brand-navy); line-height: 1;
  }

  .band { position: absolute; left: 0; right: 0; top: 268px; height: 36px; background: var(--brand-sky); }
  .band-rule { position: absolute; left: 0; right: 0; height: 2px; background: var(--brand-navy); }
  .band-rule--top { top: 261px; }
  .band-rule--bottom { top: 309px; }
  .holder { position: absolute; left: 300px; top: 268px; height: 36px; display: flex; align-items: center; gap: 8px; font-family: "Arimo", sans-serif; }
  .holder__name { font-weight: 700; font-size: 27px; color: var(--brand-navy); }
  .holder__title { font-size: 21px; color: #ffffff; }

  .address {
    position: absolute; right: 395px; top: 332px; text-align: right;
    font-family: "Arimo", sans-serif; font-size: 18px; line-height: 27px; color: var(--ink);
  }
  .details-divider { position: absolute; left: 445px; top: 322px; width: 1px; height: 100px; background: var(--divider); }
  .contacts { position: absolute; left: 465px; top: 322px; list-style: none; font-family: "Arimo", sans-serif; font-size: 17px; line-height: 24px; color: var(--ink); }
  .contacts li { display: flex; align-items: center; gap: 8px; }
  .contacts svg { width: 14px; height: 14px; flex: none; }

  .back-brand { position: absolute; left: 0; right: 0; top: 170px; display: flex; justify-content: center; align-items: center; gap: 22px; }
  .back-brand__dot { width: 64px; height: 64px; border-radius: 50%; border: 8px solid #ffffff; }
  .back-brand__name { font-family: "Montserrat", sans-serif; font-weight: 700; font-size: 70px; letter-spacing: 6px; color: #ffffff; line-height: 1; }
  .back-web {
    position: absolute; left: 0; right: 0; top: 330px; text-align: center;
    font-family: "Arimo", sans-serif; font-size: 24px; letter-spacing: 6px; color: #ffffff;
  }
</style>
</head>
<body>
<main class="stage">
  <section class="card card--front" aria-label="Card front">
    <div class="brand">
      <span class="brand__dot"></span>
      <span class="brand__name">VELUNDA</span>
    </div>

    <div class="band-rule band-rule--top"></div>
    <div class="band"></div>
    <div class="band-rule band-rule--bottom"></div>
    <div class="holder">
      <span class="holder__name">Your Name,</span>
      <span class="holder__title">Title</span>
    </div>

    <address class="address" style="font-style: normal;">
      Street Name<br>City Name<br>State, City Zip Code
    </address>
    <div class="details-divider"></div>
    <ul class="contacts">
      <li>
        <svg viewBox="0 0 14 14" aria-hidden="true"><circle cx="7" cy="7" r="6" fill="none" stroke="#333" stroke-width="1.3"/><path d="M4.5 4 L6 4 L6.5 5.8 L5.7 6.4 Q6.4 7.9 7.6 8.3 L8.2 7.5 L10 8 L10 9.5 Q6 10 4.5 4 Z" fill="#333"/></svg>
        012-555-0147
      </li>
      <li>
        <svg viewBox="0 0 14 14" aria-hidden="true"><circle cx="7" cy="7" r="6" fill="none" stroke="#333" stroke-width="1.3"/><path d="M4.5 4 L6 4 L6.5 5.8 L5.7 6.4 Q6.4 7.9 7.6 8.3 L8.2 7.5 L10 8 L10 9.5 Q6 10 4.5 4 Z" fill="#333"/></svg>
        012-555-0147
      </li>
      <li>
        <svg viewBox="0 0 14 14" aria-hidden="true"><rect x="1" y="3" width="12" height="8" fill="#333"/><path d="M1 3 L7 8 L13 3" fill="none" stroke="#fff" stroke-width="1.2"/></svg>
        name@velunda.com
      </li>
      <li>
        <svg viewBox="0 0 14 14" aria-hidden="true"><circle cx="7" cy="7" r="6" fill="none" stroke="#333" stroke-width="1.2"/><ellipse cx="7" cy="7" rx="2.6" ry="6" fill="none" stroke="#333" stroke-width="1"/><path d="M1 7 H13 M2 4 H12 M2 10 H12" stroke="#333" stroke-width="0.9"/></svg>
        www.velunda.com
      </li>
    </ul>
  </section>

  <section class="card card--back" aria-label="Card back">
    <div class="back-brand">
      <span class="back-brand__dot"></span>
      <span class="back-brand__name">VELUNDA</span>
    </div>
    <p class="back-web">www.velunda.com</p>
  </section>
</main>
</body>
</html>
```